I need a fresh looking, exciting and loaded design for Full service Restaurant

We need a web design for our restaurant, which offers full service Pakistani and Indian food in PA, USA. Design should be elegant, simplified so customers can navigate easily and order food online for catering as well as delivery. We need loads of pictures and room to grow. I already have a web address via vemrilo.com. It should include SSL and e-commerce for ordering food.
Be original and be creative and make it a fun site :)

```html
<!DOCTYPE html>
<html lang="en">
<head>
<meta charset="utf-8">
<title>Saffron Lane – A fine Pak-Indian Cuisine</title>
<link href="https://fonts.googleapis.com/css2?family=Open+Sans:wght@400;600;700;800&family=Playfair+Display:ital,wght@0,400;1,400&display=swap" rel="stylesheet">
<style>
:root{
  --red:#d21f1f;
  --red-deep:#b3161a;
  --cream:#efe9d9;
  --cream-dark:#e4dcc4;
  --gold:#b89a5c;
  --ink:#3a3530;
  --footer:#1f1c17;
  --footer-link:#b7a073;
  --green:#2f6b2a;
}
*{box-sizing:border-box;margin:0;padding:0}
html,body{width:1200px;height:3030px;overflow:hidden}
body{font-family:"Open Sans",sans-serif;background:var(--cream);color:var(--ink)}

.site-header{height:113px;background:linear-gradient(#f1ecdd,#e8e1cc);position:relative}
.brand{position:absolute;left:100px;top:30px;display:flex;align-items:center;gap:12px}
.brand-mark{width:46px;height:46px;border-radius:50%;background:var(--green)}
.brand-name{font-weight:700;font-size:30px;color:var(--red);line-height:1}
.brand-tag{font-size:13px;color:var(--green);font-weight:600;margin-top:4px}
.delivery{position:absolute;left:640px;top:32px;display:flex;align-items:center;gap:12px}
.delivery-badge{width:62px;height:50px;border-radius:50% 50% 12px 12px;background:radial-gradient(circle at 60% 35%,#e8403a 0%,#c41a1a 55%,#8a1414 100%)}
.delivery small{display:block;font-family:"Playfair Display",serif;font-size:13px;color:#333}
.delivery strong{font-family:"Playfair Display",serif;font-weight:400;font-size:18px;color:var(--red);letter-spacing:1px}
.call{position:absolute;left:845px;top:34px;display:flex;align-items:center;gap:10px;font-family:"Playfair Display",serif;font-size:18px;color:#444}
.call-icon{width:46px;height:46px;border-radius:50%;background:var(--green);display:flex;align-items:center;justify-content:center}
.call b{color:var(--red);font-weight:400}

.main-nav{height:55px;background:linear-gradient(var(--red),var(--red-deep));display:flex;padding-left:99px}
.main-nav a{display:block;padding:10px 14px 0 0;color:#fff;text-decoration:none;border-right:1px solid rgba(255,255,255,.35)}
.main-nav a+a{padding-left:18px}
.main-nav b{display:block;font-size:12px;font-weight:700}
.main-nav span{display:block;font-size:11px}

.hero{height:464px;position:relative;background:
  radial-gradient(ellipse 30% 40% at 12% 80%,rgba(60,90,30,.55),transparent 70%),
  radial-gradient(ellipse 45% 55% at 55% 48%,#d08a2c 0%,#a85a1c 35%,transparent 75%),
  radial-gradient(ellipse 30% 35% at 90% 20%,#c9902e,transparent 70%),
  linear-gradient(135deg,#5a3418,#3a2210 60%,#24150b);text-align:center;color:#fff}
.hero-title{padding-top:106px;font-size:70px;font-weight:700;line-height:1;text-shadow:0 2px 8px rgba(0,0,0,.35)}
.hero-sub{font-size:22px;font-weight:600;margin-top:6px}
.hero-line{font-family:"Playfair Display",serif;font-size:19px;letter-spacing:3px;margin-top:18px;line-height:36px}
.hero-stars{margin-top:8px;font-size:12px;letter-spacing:8px}
.slider-dots{position:absolute;left:0;right:0;bottom:22px;display:flex;justify-content:center;gap:8px}
.slider-dots i{width:7px;height:7px;border-radius:50%;background:rgba(255,255,255,.45)}
.slider-dots i:first-child{background:#fff}

.section-title{font-weight:700;color:var(--red);font-size:30px;letter-spacing:5px;text-align:center}
.section-lead{text-align:center;font-size:10px;letter-spacing:1.5px;color:#555;margin-top:14px}

.specials{height:857px;padding-top:56px}
.dish-grid{display:grid;grid-template-columns:repeat(3,315px);column-gap:29px;row-gap:28px;margin:35px 0 0 99px}
.dish-card{height:297px;display:flex;flex-direction:column}
.dish-photo{height:214px}
.dish-label{flex:1;background:var(--red);color:#fff;text-align:center;padding-top:20px}
.dish-label b{display:block;font-size:13px;letter-spacing:1px}
.dish-label span{display:block;font-size:10px;letter-spacing:1.5px;margin-top:8px}

.menus-band{height:509px;background:
  radial-gradient(ellipse 25% 45% at 25% 55%,rgba(150,110,70,.45),transparent 70%),
  radial-gradient(ellipse 20% 35% at 62% 30%,rgba(120,80,55,.45),transparent 70%),
  radial-gradient(ellipse 20% 40% at 78% 75%,rgba(90,60,40,.5),transparent 70%),
  linear-gradient(90deg,#2e231c,#1d1612 50%,#2a1e16);text-align:center;color:#fff;padding-top:120px}
.menus-band h2{font-size:30px;letter-spacing:5px;font-weight:600}
.script{font-family:"Playfair Display",serif;font-style:italic;color:var(--gold);font-size:60px;line-height:1}
.menus-band p{width:820px;margin:28px auto 0;font-size:11px;letter-spacing:2.2px;line-height:26px}
.btn-red{display:inline-block;background:var(--red);color:#fff;font-size:11px;letter-spacing:1px;padding:11px 0;margin-top:28px;width:274px}

.events{height:584px;padding-top:58px}
.event-grid{display:grid;grid-template-columns:repeat(3,315px);column-gap:29px;margin:47px 0 0 99px}
.event-photo{height:236px;position:relative}
.event-tag{position:absolute;left:0;top:137px;width:242px;height:79px;background:var(--red);color:#fff;padding:22px 0 0 24px}
.event-tag b{display:block;font-size:14px;letter-spacing:1px}
.event-tag span{display:block;font-size:10px;letter-spacing:1px;margin-top:8px}
.event-text{font-size:11px;line-height:20px;color:#444;margin-top:12px}

.newsletter{height:258px;background:linear-gradient(var(--red),var(--red-deep));text-align:center;color:#fff;padding-top:54px}
.newsletter h2{font-size:20px;letter-spacing:4px;font-weight:700}
.newsletter .script{color:#d9b57a;font-size:54px;margin-top:2px}
.signup{display:flex;gap:26px;margin:22px 0 0 125px}
.signup span{width:291px;height:40px;border:1px solid #e6b48e;font-size:11px;letter-spacing:1px;display:flex;align-items:center;justify-content:center}
.signup .btn-gold{background:var(--gold);border-color:var(--gold);font-weight:700}

.site-footer{height:190px;background:var(--footer);text-align:center;padding-top:42px}
.footer-nav{font-size:10px;letter-spacing:1px;color:var(--footer-link);word-spacing:3px}
.footer-nav em{font-style:normal;color:#777;margin:0 24px}
.copyright{font-size:9px;color:var(--footer-link);margin-top:20px;letter-spacing:.5px}
.social{display:flex;justify-content:center;gap:12px;margin-top:36px}
.social i{width:26px;height:26px;border-radius:50%;background:var(--footer-link)}
</style>
</head>
<body>
<header class="site-header">
  <div class="brand">
    <div class="brand-mark"></div>
    <div><div class="brand-name">Saffron Lane</div><div class="brand-tag">A fine Pak-Indian Cuisine</div></div>
  </div>
  <div class="delivery">
    <div class="delivery-badge" role="img" aria-label="Delivery rider on a scooter"></div>
    <div><small>FREE DOOR</small><strong>DELIVERY</strong></div>
  </div>
  <div class="call">
    <div class="call-icon"><svg width="22" height="22" viewBox="0 0 24 24"><path fill="#fff" d="M6.6 10.8a15 15 0 0 0 6.6 6.6l2.2-2.2c.3-.3.7-.4 1-.2 1.1.4 2.3.6 3.6.6.6 0 1 .4 1 1V20c0 .6-.4 1-1 1A17 17 0 0 1 3 4c0-.6.4-1 1-1h3.5c.6 0 1 .4 1 1 0 1.3.2 2.5.6 3.6.1.3 0 .7-.2 1z"/></svg></div>
    <span>CALL US : <b>( 6520 ) 555 014</b></span>
  </div>
</header>
<nav class="main-nav">
  <a href="#" style="width:162px"><b>HOME</b><span>Welcome to Saffron Lane</span></a>
  <a href="#" style="width:143px"><b>ABOUT US</b><span>Know our History</span></a>
  <a href="#" style="width:156px"><b>MENUS</b><span>View our foods</span></a>
  <a href="#" style="width:178px"><b>EVENTS</b><span>view our upcoming events</span></a>
  <a href="#" style="width:169px"><b>PHOTO GALLERY</b><span>Our service Photos</span></a>
  <a href="#" style="width:160px"><b>CONTACT US</b><span>Get in touch</span></a>
</nav>
<section class="hero" role="img" aria-label="Photo of a bowl of curry with chillies and spices">
  <div class="hero-title">Saffron Lane</div>
  <div class="hero-sub">A fine Pak-Indian Cuisine</div>
  <div class="hero-line">WE OFFER FULL SERVICE PAKISTANI AND INDIAN FOOD<br>IN PHILADELPHIA, USA</div>
  <div class="hero-stars">★ ★ ★ ★ ★</div>
  <div class="slider-dots"><i></i><i></i><i></i><i></i></div>
</section>
<section class="specials">
  <h2 class="section-title">SPECIAL MENUS</h2>
  <p class="section-lead">LOREM IPSUM IS SIMPLY DUMMY TEXT OF THE PRINTING AND TYPESETTING INDUSTRY.</p>
  <div class="dish-grid">
    <div class="dish-card"><div class="dish-photo" role="img" aria-label="Steak with asparagus" style="background:radial-gradient(ellipse 60% 50% at 40% 70%,#7a4630,transparent 75%),radial-gradient(ellipse 40% 30% at 70% 35%,#6f8a3a,transparent 75%),linear-gradient(160deg,#2c1e18,#4a2c20 60%,#1e1410)"></div><div class="dish-label"><b>LOREM IPSUM IS SIMPLY</b><span>CLICK HERE FOR VIEW DETAILS ➜</span></div></div>
    <div class="dish-card"><div class="dish-photo" role="img" aria-label="Sliced grilled duck with greens" style="background:radial-gradient(ellipse 55% 40% at 50% 35%,#a86a48,transparent 75%),radial-gradient(ellipse 50% 30% at 50% 78%,#5f7a32,transparent 75%),linear-gradient(160deg,#d9c8b4,#b89478)"></div><div class="dish-label"><b>LOREM IPSUM IS SIMPLY</b><span>CLICK HERE FOR VIEW DETAILS ➜</span></div></div>
    <div class="dish-card"><div class="dish-photo" role="img" aria-label="Braised chicken with olives and herbs" style="background:radial-gradient(ellipse 40% 30% at 50% 30%,#5a8a34,transparent 75%),radial-gradient(ellipse 60% 45% at 50% 70%,#a8461e,transparent 75%),linear-gradient(160deg,#e89a50,#6a2414)"></div><div class="dish-label"><b>LOREM IPSUM IS SIMPLY</b><span>CLICK HERE FOR VIEW DETAILS ➜</span></div></div>
    <div class="dish-card"><div class="dish-photo" role="img" aria-label="Glazed chicken with rice and vegetables" style="background:radial-gradient(ellipse 50% 35% at 60% 40%,#d08a30,transparent 75%),radial-gradient(ellipse 70% 30% at 40% 85%,#f4efe6,transparent 75%),radial-gradient(ellipse 25% 30% at 12% 30%,#5c8a36,transparent 75%),linear-gradient(160deg,#c98a40,#e8dccb)"></div><div class="dish-label"><b>LOREM IPSUM IS SIMPLY</b><span>CLICK HERE FOR VIEW DETAILS ➜</span></div></div>
    <div class="dish-card"><div class="dish-photo" role="img" aria-label="Grilled meat with rice and green beans" style="background:radial-gradient(ellipse 45% 30% at 55% 30%,#d8d0b8,transparent 75%),radial-gradient(ellipse 55% 40% at 40% 70%,#6a3e24,transparent 75%),radial-gradient(ellipse 30% 25% at 70% 55%,#9a2e28,transparent 75%),linear-gradient(160deg,#8a7a64,#3e2a1c)"></div><div class="dish-label"><b>LOREM IPSUM IS SIMPLY</b><span>CLICK HERE FOR VIEW DETAILS ➜</span></div></div>
    <div class="dish-card"><div class="dish-photo" role="img" aria-label="Grilled salmon fillet" style="background:radial-gradient(ellipse 55% 40% at 50% 62%,#e27a3a,transparent 75%),radial-gradient(ellipse 40% 25% at 60% 25%,#7a8a3a,transparent 75%),linear-gradient(160deg,#f2dcae,#d8a060)"></div><div class="dish-label"><b>LOREM IPSUM IS SIMPLY</b><span>CLICK HERE FOR VIEW DETAILS ➜</span></div></div>
  </div>
</section>
<section class="menus-band" role="img" aria-label="Dim photo of a couple dining by candlelight">
  <h2>SAFFRON LANE</h2>
  <div class="script">Menus</div>
  <p>LOREM IPSUM IS SIMPLY DUMMY TEXT OF THE PRINTING AND TYPESETTING INDUSTRY. LOREM IPSUM HAS BEEN THE INDUSTRY'S STANDARD DUMMY TEXT EVER SINCE THE 1500S, WHEN AN UNKNOWN PRINTER TOOK A GALLEY OF TYPE AND SCRAMBLED</p>
  <span class="btn-red">CLICK HERE FOR VIEW OUR MENUS</span>
</section>
<section class="events">
  <h2 class="section-title">RECENT EVENTS</h2>
  <p class="section-lead">LOREM IPSUM IS SIMPLY DUMMY TEXT OF THE PRINTING AND TYPESETTING INDUSTRY.</p>
  <div class="event-grid">
    <article><div class="event-photo" role="img" aria-label="Couple at a restaurant table" style="background:radial-gradient(ellipse 30% 45% at 30% 40%,#8a5a4a,transparent 75%),radial-gradient(ellipse 30% 50% at 75% 45%,#3a3040,transparent 75%),linear-gradient(160deg,#6a2a2e,#2a1618)"><div class="event-tag"><b>LOREM IPSUM IS SIMPLY</b><span>ON 27 FEBRAURY 2016</span></div></div><p class="event-text">Lorem Ipsum is simply dummy text of the printing and typesetting industry. Lorem Ipsum has been the industry's standard dummy text ever since the 1500s, when an unknown printer took a galley...</p></article>
    <article><div class="event-photo" role="img" aria-label="Guests toasting with wine" style="background:radial-gradient(ellipse 35% 40% at 30% 30%,#e0b070,transparent 75%),radial-gradient(ellipse 30% 40% at 70% 45%,#7a2a24,transparent 75%),linear-gradient(160deg,#8a5a30,#2a1a10)"><div class="event-tag"><b>LOREM IPSUM IS SIMPLY</b><span>ON 27 FEBRAURY 2016</span></div></div><p class="event-text">Lorem Ipsum is simply dummy text of the printing and typesetting industry. Lorem Ipsum has been the industry's standard dummy text ever since the 1500s, when an unknown printer took a galley...</p></article>
    <article><div class="event-photo" role="img" aria-label="Waiting staff serving a table" style="background:radial-gradient(ellipse 30% 50% at 35% 50%,#2a2622,transparent 75%),radial-gradient(ellipse 25% 45% at 78% 55%,#33302c,transparent 75%),linear-gradient(160deg,#f2f0ea,#bcb6aa)"><div class="event-tag"><b>LOREM IPSUM IS SIMPLY</b><span>ON 27 FEBRAURY 2016</span></div></div><p class="event-text">Lorem Ipsum is simply dummy text of the printing and typesetting industry. Lorem Ipsum has been the industry's standard dummy text ever since the 1500s, when an unknown printer took a galley...</p></article>
  </div>
</section>
<section class="newsletter">
  <h2>GET OUR RECENT UPDATES THROUGH OUR</h2>
  <div class="script">Newsletter</div>
  <div class="signup"><span>- NAME -</span><span>- EMAIL -</span><span class="btn-gold">SUBSCRIBE NOW</span></div>
</section>
<footer class="site-footer">
  <div class="footer-nav">HOME<em>/</em>ABOUT US<em>/</em>SERVICES<em>/</em>MENUS<em>/</em>PHOTO GALLERY<em>/</em>LOCATION<em>/</em>CONTACT US</div>
  <div class="copyright">COPYRIGHTS © 2016, SAFFRON LANE. ALL RIGHTS RESERVED.</div>
  <div class="social"><i></i><i></i><i></i><i></i><i></i></div>
</footer>
</body>
</html>
```